High Tech Real Estate Startup needs a business card

We are developing an innovative real estate marketing product based around advanced search and virtual reality.

We talk to people, we need business cards.

Target Market(s)

The target market is technology professionals and realtors.

Contact Information for Business Card

The information to be included will include

Name
Title
Phone Number
E-mail Address
www.zelquin.com

It should use simple iconography for each one of those fields.

Font styles to use
Other font styles liked:
• Co, Jubilat, Avenir

Colors

Designer to choose colors to be used in the design.

Requirements
Must have
• Clean aesthetic,
• Good use of negative space.
• It should use our company logo, shown in the attached file. It is able to use the negative of that logo (coloured font and white background) and I have attached other acceptable accent colours in a swatch file.
Should not have
• Should not be too busy
• No extraneous text (slogans, tag lines etc)

```html
<!DOCTYPE html>
<html lang="en">
<head>
<meta charset="UTF-8">
<title>Zelquin Business Card</title>
<link href="https://fonts.googleapis.com/css2?family=Open+Sans:wght@400;600&display=swap" rel="stylesheet">
<style>
  :root {
    --backdrop: #3b3b3d;
    --card: #1d1d20;
    --accent: #3ecfc9;
    --ink-light: #e8e8e8;
    --rule: #4a4a4e;
  }
  * { margin: 0; padding: 0; box-sizing: border-box; }
  html, body {
    width: 800px;
    height: 1200px;
    overflow: hidden;
    background: var(--backdrop);
  }
  .canvas {
    width: 800px;
    height: 1200px;
    position: relative;
  }
  .card {
    position: absolute;
    left: 60px;
    width: 680px;
    height: 390px;
    background: var(--card);
    border-radius: 28px;
    box-shadow: 0 12px 30px rgba(0,0,0,0.35);
  }
  .card--front { top: 170px; }
  .card--back { top: 640px; }

  .brand {
    position: absolute;
    inset: 0;
    display: flex;
    align-items: center;
    justify-content: center;
    gap: 18px;
  }
  .brand__mark {
    width: 22px;
    height: 22px;
    background: var(--ink-light);
  }
  .brand__name {
    font-family: "Open Sans", sans-serif;
    font-weight: 600;
    font-size: 54px;
    line-height: 1;
    color: var(--ink-light);
  }

  .identity {
    position: absolute;
    right: 370px;
    top: 165px;
    text-align: right;
    font-family: "Open Sans", sans-serif;
  }
  .identity__name {
    font-size: 25px;
    font-weight: 600;
    color: var(--accent);
    line-height: 1.2;
    white-space: nowrap;
  }
  .identity__title {
    font-size: 14px;
    color: var(--ink-light);
    margin-top: 6px;
    white-space: nowrap;
  }

  .divider {
    position: absolute;
    left: 336px;
    top: 130px;
    width: 1px;
    height: 130px;
    background: var(--rule);
  }

  .contact-list {
    position: absolute;
    left: 356px;
    top: 152px;
    list-style: none;
    font-family: "Open Sans", sans-serif;
    font-size: 15px;
    color: var(--ink-light);
  }
  .contact-list__item {
    display: flex;
    align-items: center;
    height: 28px;
    white-space: nowrap;
  }
  .contact-list__icon {
    width: 14px;
    height: 14px;
    margin-right: 16px;
    flex: none;
  }
</style>
</head>
<body>
<main class="canvas">
  <section class="card card--front">
    <div class="brand">
      <span class="brand__mark"></span>
      <span class="brand__name">Zelquin</span>
    </div>
  </section>

  <section class="card card--back">
    <div class="identity">
      <div class="identity__name">John Doe Smith</div>
      <div class="identity__title">Managing Director</div>
    </div>
    <div class="divider"></div>
    <ul class="contact-list">
      <li class="contact-list__item">
        <svg class="contact-list__icon" viewBox="0 0 16 16" aria-hidden="true">
          <path fill="var(--accent)" d="M3.5 1.5l2.5 0 1.2 3.2-1.6 1.2c.8 1.8 2.2 3.2 4 4l1.2-1.6 3.2 1.2v2.5c0 .8-.7 1.5-1.5 1.5C6.6 13.5 2.5 9.4 2 3c0-.8.7-1.5 1.5-1.5z"/>
        </svg>
        555.555.5555
      </li>
      <li class="contact-list__item">
        <svg class="contact-list__icon" viewBox="0 0 16 16" aria-hidden="true">
          <rect x="1.5" y="3.5" width="13" height="9" rx="1" fill="none" stroke="var(--accent)" stroke-width="1.5"/>
          <path d="M2 4l6 5 6-5" fill="none" stroke="var(--accent)" stroke-width="1.5"/>
        </svg>
        john.doe@zelquin.com
      </li>
      <li class="contact-list__item">
        <svg class="contact-list__icon" viewBox="0 0 16 16" aria-hidden="true">
          <circle cx="8" cy="8" r="6.3" fill="none" stroke="var(--accent)" stroke-width="1.4"/>
          <ellipse cx="8" cy="8" rx="2.8" ry="6.3" fill="none" stroke="var(--accent)" stroke-width="1.2"/>
          <path d="M1.8 8h12.4" stroke="var(--accent)" stroke-width="1.2"/>
        </svg>
        www.zelquin.com
      </li>
    </ul>
  </section>
</main>
</body>
</html>
```